Need help in designing new business card utilizing our new logo.

BuildMark Solutions works with Construction Business Owners, Managers & IT Professionals to strengthen software usage and increase user productivity.

Our Construction Accounting and Mobile Field Management Software Clients engage with us in the following areas:

New Software Implementations
Software Re-Implementations
Redesigning Software Usage at the User Level
Project Coordination & Management
Continued Software Support

Old tag line:
Weighing Options - Implementing Solutions

www.buildmark-solutions.example

Ridge 4 is a product, but not needed for a new business card.

```html
<!DOCTYPE html>
<html lang="en">
<head>
<meta charset="utf-8">
<title>BuildMark Solutions – Business Card</title>
<link rel="stylesheet" href="https://fonts.googleapis.com/css2?family=Roboto:wght@400;500;700&family=Roboto+Condensed:wght@700&display=swap">
<style>
  :root {
    --navy: #0c1a96;
    --ink: #2b2b2b;
    --muted: #777;
    --card: #f1f1f1;
    --card-edge: #e4e4e4;
    --backdrop: #b9b9b9;
    --white: #ffffff;
  }
  * { box-sizing: border-box; margin: 0; padding: 0; }
  html, body { width: 1200px; height: 576px; overflow: hidden; }
  body {
    background: var(--backdrop);
    font-family: "Roboto", Arial, sans-serif;
    position: relative;
  }
  .card {
    position: absolute;
    top: 138px;
    width: 484px;
    height: 293px;
    border-radius: 14px;
    background: linear-gradient(135deg, var(--white) 0%, var(--card) 55%, var(--card-edge) 100%);
    box-shadow: 0 3px 6px rgba(0,0,0,0.25);
    overflow: hidden;
  }
  .card--front { left: 82px; }
  .card--back { left: 602px; }

  /* Front */
  .front-brand {
    position: absolute;
    top: 0; left: 0; right: 0;
    height: 168px;
    display: flex;
    align-items: center;
    justify-content: center;
    gap: 12px;
  }
  .brand-square {
    width: 34px; height: 34px;
    background: var(--navy);
  }
  .brand-name {
    font-family: "Roboto", Arial, sans-serif;
    font-weight: 700;
    font-size: 32px;
    color: var(--navy);
    letter-spacing: 0.5px;
  }
  .services-band {
    position: absolute;
    top: 168px; left: 0; right: 0;
    height: 80px;
    background: var(--navy);
    color: var(--white);
    font-size: 13px;
    line-height: 18.5px;
    text-align: center;
    padding-top: 12px;
  }
  .services-band .sep { margin: 0 9px; }
  .front-web {
    position: absolute;
    top: 262px; left: 0; right: 0;
    display: flex;
    align-items: center;
    justify-content: center;
    gap: 18px;
    font-size: 12px;
    color: var(--navy);
  }
  .front-web .rule {
    width: 38px; height: 1px;
    background: linear-gradient(90deg, transparent, var(--muted), transparent);
  }

  /* Back */
  .accent-dot {
    position: absolute;
    left: -54px; top: 34px;
    width: 60px; height: 60px;
    border-radius: 50%;
    background: var(--navy);
  }
  .holder-name {
    position: absolute;
    left: 24px; top: 48px;
    font-family: "Roboto Condensed", "Arial Narrow", sans-serif;
    font-weight: 700;
    font-size: 22px;
    color: var(--navy);
  }
  .holder-title {
    position: absolute;
    left: 24px; top: 78px;
    font-size: 12px;
    color: var(--ink);
  }
  .address {
    position: absolute;
    left: 22px; top: 156px;
    font-size: 12.5px;
    line-height: 17px;
    color: var(--ink);
  }
  .contacts {
    position: absolute;
    left: 22px; top: 199px;
    list-style: none;
    font-size: 12.5px;
    line-height: 17px;
    color: var(--ink);
  }
  .contacts li { display: flex; align-items: center; gap: 11px; }
  .contacts svg { width: 10px; height: 10px; fill: var(--navy); flex: none; }
  .back-brand {
    position: absolute;
    right: 26px; top: 206px;
    display: flex;
    align-items: center;
    gap: 8px;
  }
  .back-brand .brand-square { width: 22px; height: 22px; }
  .back-brand .brand-name { font-size: 21px; }
</style>
</head>
<body>
  <section class="card card--front">
    <div class="front-brand">
      <span class="brand-square"></span>
      <span class="brand-name">BuildMark Solutions</span>
    </div>
    <div class="services-band">
      <p>New Software Implementations<span class="sep">|</span>Software Re-Implementations</p>
      <p>Redesigning Software Usage at the User Level</p>
      <p>Project Coordination &amp; Management<span class="sep">|</span>Continued Software Support</p>
    </div>
    <div class="front-web">
      <span class="rule"></span>
      <span>www.buildmark-solutions.example</span>
      <span class="rule"></span>
    </div>
  </section>

  <section class="card card--back">
    <span class="accent-dot"></span>
    <h1 class="holder-name">Dana R. Whitfield</h1>
    <p class="holder-title">Owner</p>
    <address class="address" style="font-style:normal">
      14B Harbor Street - PMB 118<br>
      Millbrook Falls, NY 12000
    </address>
    <ul class="contacts">
      <li>
        <svg viewBox="0 0 10 10" aria-hidden="true"><path d="M2.5 0h5a1 1 0 0 1 1 1v8a1 1 0 0 1-1 1h-5a1 1 0 0 1-1-1V1a1 1 0 0 1 1-1zm.5 1.3v6.2h4V1.3z"/></svg>
        555-014-2290
      </li>
      <li>
        <svg viewBox="0 0 10 10" aria-hidden="true"><path d="M0 3.2C0 1.5 2.2 1 5 1s5 .5 5 2.2V4H7.2V3H2.8v1H0zM2.5 5h5l1.5 4h-8z"/></svg>
        555-017-3380 ext. 100
      </li>
      <li>
        <svg viewBox="0 0 10 10" aria-hidden="true"><path d="M0 2h10v6H0zm1 .6L5 5.6l4-3z"/></svg>
        dana.whitfield@buildmark-solutions.example
      </li>
      <li>
        <svg viewBox="0 0 10 10" aria-hidden="true"><path d="M5 0a5 5 0 1 0 0 10A5 5 0 0 0 5 0zm0 1c.6 0 1.3 1.4 1.4 3.5H3.6C3.7 2.4 4.4 1 5 1zM1.1 4.5h1.5c0-1.2.3-2.2.6-2.9A4 4 0 0 0 1.1 4.5zm5.7-2.9c.4.7.6 1.7.6 2.9h1.5a4 4 0 0 0-2.1-2.9zM1.1 5.5a4 4 0 0 0 2.1 2.9c-.3-.7-.5-1.7-.6-2.9zm2.5 0c.1 2.1.8 3.5 1.4 3.5s1.3-1.4 1.4-3.5zm3.8 0c0 1.2-.3 2.2-.6 2.9a4 4 0 0 0 2.1-2.9z"/></svg>
        www.buildmark-solutions.example
      </li>
    </ul>
    <div class="back-brand">
      <span class="brand-square"></span>
      <span class="brand-name">BuildMark Solutions</span>
    </div>
  </section>
</body>
</html>
```